Business Card and Letterhead for Pimlu - modern real estate business

I need a double sided business card design for Pimlu. Please see business card brief here https://files.trelvonadocs.com/sheet/r/7QzTmWbaXLJnoPEd-kRyUgFhHsstbvCe2qfoMxDa_pz/view?mode=shared

Please feel free to design the business cards however you feel best. I am happy to give some creative freedoms and then provide feedback from there.

Please then also create a letterhead to match the business card design

Colors

Designer to choose colors to be used in the design.

Requirements
Must have
• Must be a modern, elegant business card which looks very professional

```html
<!DOCTYPE html>
<html lang="en">
<head>
<meta charset="utf-8">
<title>Pimlu — Business Card</title>
<link rel="stylesheet" href="https://fonts.googleapis.com/css2?family=Roboto:wght@400;500;700&display=swap">
<style>
  :root {
    --stage: #1d1d1d;
    --brand-red: #e60615;
    --card-white: #ffffff;
    --card-charcoal: #2a2a2a;
    --edge-black: #111111;
    --photo-tone-top: #8d9a8f;
    --photo-tone-bottom: #2e2e33;
    --photo-frame: #5a5a5a;
  }
  * { box-sizing: border-box; margin: 0; padding: 0; }
  html, body {
    width: 1125px;
    height: 1200px;
    overflow: hidden;
    background: var(--stage);
    font-family: "Roboto", Arial, sans-serif;
  }
  .card {
    position: absolute;
    left: 171px;
    width: 826px;
    height: 471px;
    overflow: hidden;
  }
  .card--front { top: 106px; background: var(--card-white); }
  .card--back { top: 640px; background: var(--card-charcoal); }

  .front-panel {
    position: absolute;
    inset: 0;
    width: 100%;
    height: 100%;
  }

  .agent-photo {
    position: absolute;
    left: 50px;
    top: 121px;
    width: 93px;
    height: 112px;
    border-radius: 8px;
    border: 2px solid var(--photo-frame);
    background: linear-gradient(180deg, var(--photo-tone-top) 0%, #b79a82 45%, var(--photo-tone-bottom) 75%);
  }

  .agent-details {
    position: absolute;
    left: 50px;
    top: 254px;
    color: var(--card-white);
  }
  .agent-name {
    font-weight: 700;
    font-size: 27px;
    line-height: 1.1;
  }
  .agent-role {
    font-weight: 500;
    font-size: 18.5px;
    margin-top: 5px;
  }
  .contact-list {
    list-style: none;
    margin-top: 24px;
    font-size: 18.5px;
    line-height: 23.5px;
  }
  .contact-list li {
    display: flex;
    align-items: center;
    gap: 10px;
  }
  .contact-icon { width: 16px; height: 16px; flex: none; }
  .postal-address {
    font-size: 18.5px;
    margin-top: 10px;
  }

  .brand-name {
    position: absolute;
    color: var(--brand-red);
    font-weight: 700;
    letter-spacing: 0.04em;
    line-height: 1;
    white-space: nowrap;
  }
  .brand-name--front {
    left: 410px;
    top: 83px;
    width: 348px;
    text-align: center;
    font-size: 80px;
  }
  .brand-name--back {
    left: 0;
    right: 0;
    top: 186px;
    text-align: center;
    font-size: 114px;
  }
</style>
</head>
<body>
  <section class="card card--front" aria-label="Business card front">
    <svg class="front-panel" viewBox="0 0 826 471" preserveAspectRatio="none" aria-hidden="true">
      <polygon points="0,0 240,0 485,471 0,471" fill="var(--brand-red)"/>
      <line x1="240" y1="0" x2="485" y2="471" stroke="var(--edge-black)" stroke-width="2.5"/>
    </svg>

    <div class="agent-photo" role="img" aria-label="Portrait photo of the agent"></div>

    <div class="agent-details">
      <h1 class="agent-name">Liam Carter</h1>
      <p class="agent-role">Licenced Real Estate Agent</p>
      <ul class="contact-list">
        <li>
          <svg class="contact-icon" viewBox="0 0 16 16" aria-hidden="true"><path fill="#fff" d="M3.5 1.5l2.3 0 1.1 3.2-1.6 1.3a9 9 0 0 0 4.7 4.7l1.3-1.6 3.2 1.1v2.3c0 .8-.7 1.5-1.5 1.5A12.5 12.5 0 0 1 2 3c0-.8.7-1.5 1.5-1.5z"/></svg>
          0400 555 218
        </li>
        <li>
          <svg class="contact-icon" viewBox="0 0 16 16" aria-hidden="true"><rect x="1.5" y="4" width="13" height="9" fill="#fff"/><path d="M1.5 4.5l6.5 4.5 6.5-4.5" fill="none" stroke="var(--brand-red)" stroke-width="1.3"/></svg>
          liam@pimlu.com
        </li>
        <li>
          <svg class="contact-icon" viewBox="0 0 16 16" aria-hidden="true"><circle cx="8" cy="8" r="7" fill="#fff"/><path d="M5 4.5c1.5.5 2 1.5 1.2 2.5S7 9 8.5 9.5 9 12 8 13.5M10.5 3.5c-.5 1 .3 2 1.5 2.3" fill="none" stroke="var(--brand-red)" stroke-width="1.4"/></svg>
          www.pimlu.com
        </li>
      </ul>
      <p class="postal-address">PO Box 1836, Glenrock NSW 2999</p>
    </div>

    <p class="brand-name brand-name--front">PIMLU</p>
  </section>

  <section class="card card--back" aria-label="Business card back">
    <p class="brand-name brand-name--back">PIMLU</p>
  </section>
</body>
</html>
```